Veldmark Supplies Business Card

Professional business card that stand out to our potential customers. Front and back with clean modern design

Industry/Entity Type

Oil and gas

Contact Information for Business Card

Name, address, website , office phone and cell number

Requirements
Must have
• Editable files for each employee

```html
<!DOCTYPE html>
<html lang="en">
<head>
<meta charset="utf-8">
<title>Veldmark Supplies Business Card</title>
<link href="https://fonts.googleapis.com/css2?family=Arimo:wght@400;700&display=swap" rel="stylesheet">
<style>
  :root {
    --backdrop: #3d3d3d;
    --brand-blue: #06aed1;
    --brand-red: #f50000;
    --paper: #ffffff;
    --ink-light: #ffffff;
  }
  * { box-sizing: border-box; margin: 0; padding: 0; }
  html, body { width: 1200px; height: 803px; overflow: hidden; }
  body {
    background: var(--backdrop);
    font-family: "Arimo", Arial, sans-serif;
    position: relative;
  }
  .card {
    position: absolute;
    top: 250px;
    width: 530px;
    height: 303px;
    border-radius: 18px;
    overflow: hidden;
    box-shadow: 0 10px 24px rgba(0,0,0,0.35);
  }
  .card-front { left: 50px; background: var(--brand-blue); }
  .card-back {
    left: 620px;
    background: var(--paper);
    border-bottom: 3px solid var(--brand-blue);
    display: flex;
    align-items: center;
    justify-content: center;
  }
  .front-white-field {
    position: absolute;
    inset: 0;
    background: var(--paper);
    clip-path: polygon(56% 0, 100% 0, 100% 100%, 82% 100%);
  }
  .front-details {
    position: absolute;
    left: 34px;
    top: 34px;
    color: var(--ink-light);
  }
  .wordmark {
    font-weight: 700;
    text-transform: uppercase;
    color: var(--brand-red);
    letter-spacing: 0.5px;
  }
  .front-details .wordmark {
    display: inline-block;
    background: var(--paper);
    padding: 4px 10px;
    font-size: 15px;
  }
  .person-name {
    margin-top: 22px;
    font-size: 26px;
    font-weight: 700;
    color: var(--brand-red);
  }
  .person-role { font-size: 14px; margin-top: 2px; }
  .address { margin-top: 16px; font-size: 14px; line-height: 1.3; }
  .contact-list { list-style: none; margin-top: 12px; font-size: 14px; line-height: 1.45; }
  .contact-list li { display: flex; align-items: center; gap: 8px; }
  .contact-icon { width: 12px; height: 12px; flex: none; }
  .back-brand { display: flex; align-items: center; gap: 12px; }
  .back-brand .wordmark { font-size: 30px; }
  .brand-square { width: 22px; height: 22px; background: var(--brand-blue); }
</style>
</head>
<body>
  <section class="card card-front" aria-label="Business card front">
    <div class="front-white-field"></div>
    <div class="front-details">
      <span class="wordmark">Veldmark Supplies</span>
      <p class="person-name">Daniel Reyes</p>
      <p class="person-role">President</p>
      <p class="address">4210 Ridgeway Drive<br>Midland, Texas 79701</p>
      <ul class="contact-list">
        <li>
          <svg class="contact-icon" viewBox="0 0 12 12"><path d="M2 1h3l1 3-2 1c1 2 2 3 3 3l1-2 3 1v3c-6 0-9-3-9-9z" fill="#f50000"/></svg>
          555-214-7730
        </li>
        <li>
          <svg class="contact-icon" viewBox="0 0 12 12"><rect x="3" y="0.5" width="6" height="11" rx="1" fill="none" stroke="#f50000" stroke-width="1.4"/></svg>
          555-386-1945
        </li>
        <li>
          <svg class="contact-icon" viewBox="0 0 12 12"><rect x="0.5" y="2" width="11" height="8" fill="#f50000"/><path d="M1 2.5 6 6.5 11 2.5" fill="none" stroke="#fff" stroke-width="1"/></svg>
          info@veldmarksupplies.com
        </li>
        <li>
          <svg class="contact-icon" viewBox="0 0 12 12"><circle cx="6" cy="6" r="5.5" fill="#f50000"/><path d="M0.5 6h11M6 0.5c-3 3-3 8 0 11M6 0.5c3 3 3 8 0 11" fill="none" stroke="#fff" stroke-width="0.8"/></svg>
          www.veldmarksupplies.com
        </li>
      </ul>
    </div>
  </section>

  <section class="card card-back" aria-label="Business card back">
    <div class="back-brand">
      <span class="brand-square"></span>
      <span class="wordmark">Veldmark Supplies</span>
    </div>
  </section>
</body>
</html>
```